Hard-File Archival Services Billboard (Digitization Service) for Attorneys/Law Firms

I need a billboard design for my company "Velkor Legal Aides" that advertises our primary service: Digitization of closed client files, for law firms and attorneys. Our system works as follows: 1) We get a call about a firm that wants to digitize their archived (closed) client files (which usually find their way to file cabinets or bankers boxes), 2) We go and pick those up from the law firm, 3) We bring them to our digitization facility, scan them in, and convert them into searchable PDF/A files, and 4) We upload them on the cloud, give the client a URL to visit their files whenever they want, and we delete them when requested by the client (usually for the retention duration for Missouri's rules of professional conduct, which is 6 years). It would be really cool to see "Velkor Legal Aides" and the logo clearly on the billboard, some simple sentence relating to "Missouri's best digitizing and cloud storage service for closed client files for attorneys" (or something shorter, you get the point), with maybe a linear set of photos and arrows (as follows 1. A photo of a file cabinet opened with files hanging out of it, 2. an arrow pointing to a person scanning in documents in a big scanner (maybe with a Velkor Legal Aidez logo on it?), 3. An arrow pointing to a "secure" appearing cloud (representing cloud storage), and 4. the client sitting at a computer with an arrow pointing back to the cloud (showing the client is accessing the cloud files through the computer). Our website is www.velkorlegalaides.example if you want to glean any additional information from there. Thanks! Oh yes, I should also say the billboard dimensions (in the event you need this for photo aspect ratio) will be as follows: 14 feet tall by 48 feet wide.
Target Market(s)
Attorneys in Springfield, Missouri
Industry/Entity Type
Legal
Look and feel

```html
<!DOCTYPE html>
<html lang="en">
<head>
<meta charset="utf-8">
<title>Velkor Legal Aides – Billboard</title>
<link rel="stylesheet" href="https://fonts.googleapis.com/css2?family=Oswald:wght@500;600;700&family=Roboto:wght@500&display=swap">
<style>
  :root {
    --page-bg: #e7e9ec;
    --board-dark: #141414;
    --board-mid: #1e1e1e;
    --ink-white: #f4f4f4;
    --ink-silver: #d9d9d9;
    --accent-orange: #e8921c;
  }
  * { margin: 0; padding: 0; box-sizing: border-box; }
  html, body {
    width: 1200px;
    height: 900px;
    overflow: hidden;
    background: var(--page-bg);
  }
  .billboard {
    position: absolute;
    left: 40px;
    top: 286px;
    width: 1120px;
    height: 327px;
    background: radial-gradient(ellipse at 60% 40%, var(--board-mid), var(--board-dark) 75%);
    overflow: hidden;
  }
  .brand {
    position: absolute;
    left: 58px;
    top: 86px;
    width: 270px;
    height: 160px;
    display: flex;
    align-items: center;
    gap: 16px;
  }
  .brand-dot {
    flex: none;
    width: 44px;
    height: 44px;
    border-radius: 50%;
    background: var(--ink-white);
  }
  .brand-name {
    font-family: "Oswald", sans-serif;
    font-weight: 600;
    color: var(--ink-white);
    text-transform: uppercase;
    line-height: 1.02;
  }
  .brand-name .line-1 { display: block; font-size: 52px; letter-spacing: 1px; }
  .brand-name .line-2 { display: block; font-size: 29px; letter-spacing: 0.5px; }
  .tagline {
    position: absolute;
    left: 361px;
    top: 64px;
    font-family: "Roboto", sans-serif;
    font-weight: 500;
    font-size: 24px;
    color: var(--ink-white);
    text-transform: uppercase;
    letter-spacing: -0.2px;
    white-space: nowrap;
  }
  .tagline .highlight { color: var(--accent-orange); }
  .headline {
    position: absolute;
    left: 357px;
    top: 84px;
    font-family: "Oswald", sans-serif;
    font-weight: 700;
    font-size: 136px;
    line-height: 1;
    color: var(--ink-silver);
    background: linear-gradient(180deg, #ffffff 0%, #e2e2e2 55%, #b9b9b9 100%);
    -webkit-background-clip: text;
    background-clip: text;
    -webkit-text-fill-color: transparent;
    text-transform: uppercase;
    letter-spacing: 1px;
    white-space: nowrap;
  }
  .service-line {
    position: absolute;
    left: 361px;
    top: 232px;
    font-family: "Oswald", sans-serif;
    font-weight: 500;
    font-size: 50px;
    line-height: 1;
    color: var(--ink-white);
    text-transform: uppercase;
    letter-spacing: 0.3px;
    white-space: nowrap;
  }
  .cursor-icon {
    position: absolute;
    left: 739px;
    top: 270px;
    width: 26px;
    height: 34px;
  }
</style>
</head>
<body>
  <section class="billboard" aria-label="Velkor Legal Aides billboard">
    <div class="brand">
      <span class="brand-dot" aria-hidden="true"></span>
      <span class="brand-name"><span class="line-1">Velkor</span><span class="line-2">Legal Aides</span></span>
    </div>
    <p class="tagline">Missouri’s <span class="highlight">Best</span> Digitizing &amp; Cloud Storage Service</p>
    <h1 class="headline">Legal Aides</h1>
    <p class="service-line">Digitizing Services for Attorneys</p>
    <svg class="cursor-icon" viewBox="0 0 26 34" aria-hidden="true">
      <path d="M2 2 L2 26 L8 20 L13 31 L17 29 L12 18 L21 18 Z" fill="var(--accent-orange)"/>
    </svg>
  </section>
</body>
</html>
```